Building Maintenance Company Capability Statement

We would like a capability statement designed please.

Let us know where we can supply the written text.

Ideally, most of the information will be on our website.
www.tallowbridgeco.com.au

Low design quality

Target Market(s)

Strata and building managers. schools and educational facilities, retirement and aged care.

Industry/Entity Type

Building

Font styles to use
Other font styles liked:
• nanito sans light

Requirements
Must have
• Images of people working (we can supply)
Easy to skim read
Colourful and attractive
Should not have
• lots of words

```html
<!DOCTYPE html>
<html lang="en">
<head>
<meta charset="utf-8">
<title>Tallow Bridge Co – Capability Statement</title>
<link rel="stylesheet" href="https://fonts.googleapis.com/css2?family=Montserrat:wght@300;400;500;600;700;800&family=Oswald:wght@600&display=swap">
<style>
:root{
  --red:#d21f34;
  --navy:#123f78;
  --blue:#1a75c4;
  --panel:#e4e4e4;
  --ink:#1f2a3a;
  --white:#ffffff;
}
*{margin:0;padding:0;box-sizing:border-box}
html,body{width:783px;height:1200px;overflow:hidden;background:var(--white)}
body{font-family:"Montserrat",sans-serif;color:var(--ink)}
.page{position:relative;width:783px;height:1200px;overflow:hidden;background:var(--white)}

.brand{position:absolute;left:40px;top:62px;display:flex;align-items:center;gap:14px}
.brand-dot{width:60px;height:60px;border-radius:50%;background:var(--blue)}
.brand-name{font-family:"Montserrat",sans-serif;font-weight:800;font-size:28px;color:var(--red);letter-spacing:.5px;line-height:1}

.hero-band{position:absolute;left:0;top:158px;width:540px;height:331px;background:var(--red)}
.hero-text{position:absolute;left:42px;top:182px;color:var(--white)}
.hero-kicker{font-weight:300;font-size:38px;letter-spacing:1px;line-height:46px}
.hero-line{font-family:"Oswald",sans-serif;font-weight:600;font-size:42px;line-height:54px;letter-spacing:.3px;white-space:nowrap}
.hero-strong{font-weight:800;font-size:40px;line-height:48px;letter-spacing:.5px;white-space:nowrap}
.hero-rule{width:80px;height:3px;background:var(--white);margin:16px 0 20px}
.hero-sub{font-weight:400;font-size:18px;line-height:23px;width:340px}

.hero-art{position:absolute;left:0;top:0}

.services{position:absolute;left:65px;top:489px;width:325px;height:556px;background:var(--panel);border-radius:0 0 20px 20px}
.services-head{position:absolute;left:40px;top:522px;width:338px;height:71px;background:var(--navy);border-radius:0 6px 6px 0;color:var(--white);font-size:20px;line-height:24px;padding:12px 0 0 46px}
.services-head b{font-weight:700}
.services-fold{position:absolute;left:40px;top:593px}
.service-list{position:absolute;left:86px;top:642px;list-style:none}
.service{display:flex;align-items:flex-start;font-size:18.5px;line-height:23px;color:var(--ink);margin-bottom:14px}
.service svg{width:28px;height:24px;margin-right:21px;flex:none;stroke:var(--navy);fill:none;stroke-width:1.6}

.about{position:absolute;left:415px;top:555px;width:330px}
.about-title{font-size:20px;font-weight:500;color:var(--ink)}
.about-title b{color:var(--navy);font-weight:700}
.about-rule{width:72px;height:3px;background:var(--navy);margin:6px 0 20px}
.about-lead{font-size:18px;font-weight:500;line-height:23px;margin-bottom:14px}
.about-body{font-size:16px;font-weight:300;line-height:19.5px;width:320px}
.about-photo{position:absolute;left:417px;top:808px;width:320px;height:237px;border-radius:6px;background:linear-gradient(135deg,#c9d3dc 0%,#7a8da0 35%,#3aa8d8 60%,#d8c46a 100%)}

.footer-art{position:absolute;left:0;top:1060px}
.footer{position:absolute;left:0;top:1092px;width:783px;height:80px;color:var(--white);font-size:10.5px;line-height:13px}
.footer-col{position:absolute;top:6px}
.footer-col b{font-weight:700;font-size:11px}
.col-a{left:43px}
.col-b{left:240px}
.col-c{left:485px;top:30px}
.divider{position:absolute;top:0;width:1px;height:74px;background:var(--white)}
.follow{margin-bottom:12px}
</style>
</head>
<body>
<div class="page">

  <div class="brand">
    <span class="brand-dot"></span>
    <span class="brand-name">TALLOW BRIDGE CO</span>
  </div>

  <div class="hero-band"></div>

  <svg class="hero-art" width="783" height="600" viewBox="0 0 783 600">
    <g fill="var(--blue)">
      <rect x="531" y="58" width="24" height="24" transform="rotate(-35 543 70)"/>
      <rect x="598" y="30" width="24" height="24" transform="rotate(-15 610 42)"/>
      <rect x="668" y="25" width="24" height="24" transform="rotate(5 680 37)"/>
      <rect x="733" y="41" width="24" height="24" transform="rotate(22 745 53)"/>
    </g>
    <circle cx="614" cy="300" r="190" fill="var(--white)"/>
    <path d="M514 127 A200 200 0 0 0 649 497" fill="none" stroke="var(--blue)" stroke-width="18"/>
    <path d="M451 394 A188 188 0 0 0 700 470" fill="none" stroke="var(--navy)" stroke-width="14"/>
    <polygon points="705,489 783,489 748,560" fill="var(--navy)"/>
    <defs>
      <linearGradient id="workerTone" x1="0" y1="0" x2="1" y2="1">
        <stop offset="0" stop-color="#b9bec4"/>
        <stop offset=".45" stop-color="#d9d94a"/>
        <stop offset=".75" stop-color="#e2d93c"/>
        <stop offset="1" stop-color="#3b4d6e"/>
      </linearGradient>
    </defs>
    <circle cx="614" cy="300" r="172" fill="url(#workerTone)" role="img" aria-label="Photo of a tradesperson in a hi-vis uniform working on a window frame"/>
  </svg>

  <div class="hero-text">
    <p class="hero-kicker">WE ARE:</p>
    <p class="hero-line">TRUSTED RELIABLE</p>
    <p class="hero-strong">EXPERIENCED</p>
    <div class="hero-rule"></div>
    <p class="hero-sub">We Provide Cost Effective Solutions To Your Building And Maintenance Requirements.</p>
  </div>

  <div class="services"></div>
  <div class="services-head">We Provide <b>The Following Services</b></div>
  <svg class="services-fold" width="26" height="22" viewBox="0 0 26 22"><polygon points="0,0 26,0 26,22" fill="var(--navy)"/></svg>

  <ul class="service-list">
    <li class="service"><svg viewBox="0 0 28 24"><rect x="3" y="4" width="9" height="18"/><rect x="14" y="9" width="10" height="13"/><path d="M6 8h3M6 12h3M6 16h3M17 13h4M17 17h4M1 22h26"/></svg><span>Building Refurbishment<br>And Upgrade Works</span></li>
    <li class="service" style="margin-top:6px"><svg viewBox="0 0 28 24"><circle cx="12" cy="7" r="4"/><path d="M4 22c0-5 4-8 8-8s8 3 8 8z"/><rect x="19" y="14" width="7" height="5"/></svg><span>Internal And External<br>Painting Works</span></li>
    <li class="service"><svg viewBox="0 0 28 24"><circle cx="12" cy="7" r="4"/><path d="M4 22c0-5 4-8 8-8s8 3 8 8z"/><path d="M22 2l-3 6h4l-3 6"/></svg><span>Electrical</span></li>
    <li class="service"><svg viewBox="0 0 28 24"><circle cx="11" cy="6" r="4"/><path d="M4 22c0-5 3-8 7-8s7 3 7 8z"/><path d="M21 6h4v6M23 15v4"/></svg><span>Plumbing</span></li>
    <li class="service"><svg viewBox="0 0 28 24"><path d="M2 18L8 6h12l6 12zM11 6l-3 12M17 6l3 12M5 12h18"/></svg><span>Roofing</span></li>
    <li class="service"><svg viewBox="0 0 28 24"><rect x="3" y="3" width="22" height="18"/><path d="M3 9h22M3 15h22M10 3v6M18 9v6M10 15v6"/></svg><span>Plastering</span></li>
    <li class="service"><svg viewBox="0 0 28 24"><path d="M4 20L20 4l3 3L7 23zM3 22h22"/></svg><span>Carpentry And Repairs</span></li>
    <li class="service"><svg viewBox="0 0 28 24"><rect x="2" y="6" width="24" height="9" rx="1"/><path d="M5 11h18M7 18v3M11 18v3M15 18v3M19 18v3"/></svg><span>Ac Installations</span></li>
    <li class="service"><svg viewBox="0 0 28 24"><path d="M5 20c10 0 14-6 14-16C10 4 5 10 5 20zM5 20l9-10"/></svg><span>Landscaping</span></li>
  </ul>

  <section class="about">
    <h2 class="about-title">What <b>We Do</b></h2>
    <div class="about-rule"></div>
    <p class="about-lead">We Are Experienced In School, Retail and Shopping Centres, Hotel, Strata, Healthcare &amp; Retirement Villages</p>
    <p class="about-body">Our experience allows us to offer the fastest and best solutions in these work environments.</p>
  </section>
  <div class="about-photo" role="img" aria-label="Photo of a worker in a sun hat on an elevated work platform above a car park"></div>

  <svg class="footer-art" width="783" height="140" viewBox="0 0 783 140">
    <path d="M0 21 H640 C660 21 672 40 682 95 H783 V140 H0 Z" fill="var(--navy)"/>
    <path d="M0 15 H642 C668 15 682 34 692 89 H783" fill="none" stroke="var(--red)" stroke-width="5"/>
  </svg>

  <footer class="footer">
    <div class="footer-col col-a">
      <b>Brisbane And Gold Coast</b><br>Dana Whitlow<br>dana.w@tallowbridgeco.com.au<br>0400 555 017<br>PO Box 18 Harlow 4020
    </div>
    <div class="divider" style="left:218px"></div>
    <div class="footer-col col-b">
      <b>Sunshine Coast And Wide Bay</b><br>Sam Ordway<br>sam@tallowbridgeco.com.au<br>0400 555 284<br>3/12 Fernmoor Close Kelby, 4562
    </div>
    <div class="divider" style="left:461px"></div>
    <div class="footer-col col-c">
      <p class="follow">follow us</p>
      <p>www.tallowbridgeco.com.au</p>
    </div>
  </footer>

</div>
</body>
</html>
```